High-end construction company needs a business card design

We need a modern looking business card that draws people in, is memorable and looks so good people will want to sick it on their fridges.
On the first side what is needed are:
Logo
My name - Tomasz Brelwik
Title - Managing Director
Website - www.varkelt.co.uk
Email - tomasz@varkelt.co.uk
Telephone - 020 5194 6281
Mobile - 07845139072
On the back side was is needed is a list of all the services we provide:
-Kitchen Renovations
-Bathroom Renovations
-House Renovations
-Garage Conversions
-Extensions
-Loft Conversions
-Conservatories
-Carpentry
-Tiling
-Electrical
-Plumbing & Heating
-Bricklaying
-Landscaping
-Decorating
-Plastering
We would like the colours to be the same shades as on the logo with grey or black for the words.
Target Market(s)
Anyone who needs building work done
Contact Information for Business Card
This business card is for a construction company which strives to deliver excellent service and quality.
The look and feel of the card should represent this.
Requirements
Must have
- On the first side what is needed are:
Logo
My name - Tomasz Brelwik
Title - Managing Director
Website - www.varkelt.co.uk
Email - tomasz@varkelt.co.uk
Telephone - 020 5194 6281
Mobile - 07845139072
Nice to have
- Cool looking features

```html
<!DOCTYPE html>
<html lang="en">
<head>
<meta charset="utf-8">
<title>Varkelt Construction Ltd – Business Card</title>
<link rel="stylesheet" href="https://fonts.googleapis.com/css2?family=Open+Sans:wght@600;700&family=Questrial&display=swap">
<style>
  :root {
    --backdrop: #8a8a8a;
    --card-white: #ffffff;
    --card-dark: #2a2a2a;
    --green-light: #72bf44;
    --green-dark: #4a8f3f;
    --green-mid: #5fa843;
    --text-grey: #4a4a4a;
    --text-white: #ffffff;
  }
  * { margin: 0; padding: 0; box-sizing: border-box; }
  html, body {
    width: 1125px; height: 1200px; overflow: hidden;
    background: var(--backdrop);
  }
  .canvas { position: relative; width: 1125px; height: 1200px; }
  .card {
    position: absolute; left: 171px; width: 826px; height: 472px;
    overflow: hidden;
  }
  .card--front { top: 106px; background: var(--card-white); }
  .card--back { top: 640px; background: var(--card-dark); }

  .artwork-area { position: absolute; left: 0; top: 0; width: 826px; height: 472px; }

  .brand { position: absolute; color: var(--green-mid); font-family: "Open Sans", sans-serif; font-weight: 700; text-align: center; }
  .brand__name { display: block; font-size: 60px; line-height: 1; letter-spacing: 1px; }
  .brand__sub { display: block; font-size: 18px; line-height: 1; letter-spacing: 4.2px; margin-top: 8px; }
  .card--front .brand { left: 446px; top: 62px; width: 326px; }
  .card--back .brand { left: 0; right: 0; top: 178px; color: var(--green-light); }
  .card--back .brand__name { font-size: 72px; }
  .card--back .brand__sub { font-size: 19px; letter-spacing: 5px; }

  .person { position: absolute; left: 80px; top: 328px; }
  .person__name { font-family: "Open Sans", sans-serif; font-weight: 600; font-size: 26px; color: var(--green-light); line-height: 1.1; }
  .person__title { font-family: "Questrial", sans-serif; font-size: 17px; color: var(--green-mid); margin-top: 3px; }
  .contact { position: absolute; left: 82px; top: 400px; font-family: "Questrial", sans-serif; font-size: 17px; color: var(--text-grey); line-height: 25px; white-space: nowrap; }

  .services {
    position: absolute; left: 0; right: 0; top: 318px;
    font-family: "Questrial", sans-serif; font-size: 17.5px; color: var(--text-white);
    text-align: center; line-height: 23.5px; list-style: none;
  }
  .services__row { display: block; }
  .tick { display: inline-block; width: 14px; height: 12px; margin: 0 3px; vertical-align: -1px; }
</style>
</head>
<body>
<div class="canvas">

  <section class="card card--front">
    <svg class="artwork-area" viewBox="0 0 826 472" role="img" aria-label="Illustration area: green excavator arm with toothed bucket reaching across the card">
      <defs>
        <linearGradient id="artTone" x1="0" y1="0" x2="1" y2="1">
          <stop offset="0" stop-color="#72bf44"/>
          <stop offset="1" stop-color="#4a8f3f"/>
        </linearGradient>
      </defs>
      <path d="M0 0 H430 V230 H610 V472 H440 V300 H0 Z" fill="url(#artTone)" opacity="0.28"/>
    </svg>
    <div class="brand">
      <span class="brand__name">VARKELT</span>
      <span class="brand__sub">CONSTRUCTION LTD</span>
    </div>
    <div class="person">
      <p class="person__name">Tomasz Brelwik</p>
      <p class="person__title">Managing Director</p>
    </div>
    <div class="contact">
      <p>P. 020 5194 6281 C. 07845139072</p>
      <p>E. tomasz@varkelt.co.uk W. www.varkelt.co.uk</p>
    </div>
  </section>

  <section class="card card--back">
    <div class="brand">
      <span class="brand__name">VARKELT</span>
      <span class="brand__sub">CONSTRUCTION LTD</span>
    </div>
    <ul class="services">
      <li class="services__row">Kitchen Renovations<svg class="tick" viewBox="0 0 14 12"><path d="M1 6.5 L5 10 L13 1.5" fill="none" stroke="#72bf44" stroke-width="2.4"/></svg>Bathroom Renovations<svg class="tick" viewBox="0 0 14 12"><path d="M1 6.5 L5 10 L13 1.5" fill="none" stroke="#72bf44" stroke-width="2.4"/></svg>House Renovations</li>
      <li class="services__row">Garage Conversions<svg class="tick" viewBox="0 0 14 12"><path d="M1 6.5 L5 10 L13 1.5" fill="none" stroke="#72bf44" stroke-width="2.4"/></svg>Extensions<svg class="tick" viewBox="0 0 14 12"><path d="M1 6.5 L5 10 L13 1.5" fill="none" stroke="#72bf44" stroke-width="2.4"/></svg>Loft Conversions<svg class="tick" viewBox="0 0 14 12"><path d="M1 6.5 L5 10 L13 1.5" fill="none" stroke="#72bf44" stroke-width="2.4"/></svg>Conservatories</li>
      <li class="services__row">Carpentry<svg class="tick" viewBox="0 0 14 12"><path d="M1 6.5 L5 10 L13 1.5" fill="none" stroke="#72bf44" stroke-width="2.4"/></svg>Tiling<svg class="tick" viewBox="0 0 14 12"><path d="M1 6.5 L5 10 L13 1.5" fill="none" stroke="#72bf44" stroke-width="2.4"/></svg>Electrical<svg class="tick" viewBox="0 0 14 12"><path d="M1 6.5 L5 10 L13 1.5" fill="none" stroke="#72bf44" stroke-width="2.4"/></svg>Plumbing &amp; Heating<svg class="tick" viewBox="0 0 14 12"><path d="M1 6.5 L5 10 L13 1.5" fill="none" stroke="#72bf44" stroke-width="2.4"/></svg>Bricklaying</li>
      <li class="services__row">Landscaping<svg class="tick" viewBox="0 0 14 12"><path d="M1 6.5 L5 10 L13 1.5" fill="none" stroke="#72bf44" stroke-width="2.4"/></svg>Decorating<svg class="tick" viewBox="0 0 14 12"><path d="M1 6.5 L5 10 L13 1.5" fill="none" stroke="#72bf44" stroke-width="2.4"/></svg>Plastering</li>
    </ul>
  </section>

</div>
</body>
</html>
```